Lumavento business card

We need a modern business card - With our 4 colors - See web: www.lumavento.dk

I have attached logo and som old business Cards we have - Lets Make the new ones shine...:-) -

Industry/Entity Type

Business

Requirements
Must have
• the logo with lumavento only,

```html
<!DOCTYPE html>
<html lang="da">
<head>
<meta charset="utf-8">
<title>Lumavento – visitkort</title>
<link href="https://fonts.googleapis.com/css2?family=Josefin+Sans:wght@300;400&display=swap" rel="stylesheet">
<style>
  :root {
    --backdrop: #e9e6e1;
    --card: #3d3d3e;
    --lime: #7fc94e;
    --magenta: #c9358e;
    --orange: #e2833a;
    --purple: #7a2d8c;
    --text-font: "Josefin Sans", sans-serif;
  }
  * { margin: 0; padding: 0; box-sizing: border-box; }
  html, body {
    width: 1200px;
    height: 1023px;
    overflow: hidden;
    background: var(--backdrop);
    font-family: var(--text-font);
  }
  .sheet {
    position: relative;
    width: 1200px;
    height: 1023px;
  }
  .card {
    position: absolute;
    left: 320px;
    width: 560px;
    height: 362px;
    background: var(--card);
    box-shadow: 0 6px 18px rgba(0,0,0,0.18);
  }
  .card--front { top: 110px; }
  .card--back  { top: 551px; }

  .swatch {
    position: absolute;
    width: 74px;
    height: 32px;
  }
  .swatch--magenta { top: 0; right: 74px; background: var(--magenta); }
  .swatch--orange  { top: 0; right: 0;    background: var(--orange); }
  .swatch--lime    { bottom: 0; left: 0;    background: var(--lime); }
  .swatch--purple  { bottom: 0; left: 74px; background: var(--purple); }

  .brand {
    position: absolute;
    top: 50%;
    left: 50%;
    transform: translate(-50%, -50%);
    display: flex;
    align-items: center;
    gap: 14px;
    color: var(--lime);
  }
  .brand__dot {
    width: 22px;
    height: 22px;
    border-radius: 50%;
    background: var(--lime);
  }
  .brand__name {
    font-weight: 300;
    font-size: 34px;
    letter-spacing: 3px;
  }

  .contact {
    position: absolute;
    left: 48px;
    top: 56px;
  }
  .contact__name {
    color: var(--orange);
    font-size: 30px;
    font-weight: 400;
    letter-spacing: 1px;
  }
  .contact__role {
    color: var(--magenta);
    font-size: 15px;
    font-weight: 300;
    margin-top: 6px;
    letter-spacing: 1px;
  }
  .contact__details {
    margin-top: 34px;
    color: var(--lime);
    font-size: 17px;
    font-weight: 300;
    line-height: 1.65;
    letter-spacing: 0.5px;
    list-style: none;
  }
</style>
</head>
<body>
<main class="sheet">
  <section class="card card--front" aria-label="Visitkort forside">
    <span class="swatch swatch--magenta"></span>
    <span class="swatch swatch--orange"></span>
    <div class="brand">
      <span class="brand__dot"></span>
      <span class="brand__name">lumavento</span>
    </div>
    <span class="swatch swatch--lime"></span>
    <span class="swatch swatch--purple"></span>
  </section>

  <section class="card card--back" aria-label="Visitkort bagside">
    <div class="contact">
      <h1 class="contact__name">Emil Sander</h1>
      <p class="contact__role">Art Director</p>
      <ul class="contact__details">
        <li>Kastanie Allé 12</li>
        <li>2150 Nordhavn</li>
        <li>Tlf +45 31 45 27 11</li>
        <li>Mob +45 28 60 19 05</li>
      </ul>
    </div>
  </section>
</main>
</body>
</html>
```